One Pager redesign

We need our one page services descrition redesigned. You should familiarize yourself with our two websites: https://fenwavo.net/ for the colors, styles and fonts, and https://qlob.com/ for context (the site is in the process of redesign to match fenwavo.net).

I am attaching the existing "one pager." We need all the content in it to be included in the new design. The design must fit in a single 8.5 x 11 (US Letter) size page.

I look forward to reviewing your ideas!

Thank you,

-rb.

```html
<!DOCTYPE html>
<html lang="en">
<head>
<meta charset="utf-8">
<title>Fenwavo · Qlob Management Group — One Pager</title>
<link rel="stylesheet" href="https://fonts.googleapis.com/css2?family=Rajdhani:wght@500;600;700&family=Titillium+Web:wght@400;600;700&display=swap">
<style>
:root{
  --stage:#8c8c8c;
  --orange:#f0892c;
  --orange-deep:#e2641d;
  --ink:#111111;
  --cream:#f7f3ee;
  --white:#ffffff;
  --text:#3a3a3a;
  --grey:#9a9a9a;
  --logo-grey:#5a5a5a;
}
*{box-sizing:border-box;margin:0;padding:0}
html,body{width:1200px;height:960px;overflow:hidden}
body{background:var(--stage);font-family:"Titillium Web",sans-serif;color:var(--text);position:relative}
.side-label{position:absolute;top:118px;width:509px;text-align:center;font-family:"Rajdhani",sans-serif;font-weight:700;font-size:30px;letter-spacing:1px;color:#f2f2f2}
.side-label.front{left:90px}.side-label.back{left:627px}
.page{position:absolute;top:156px;width:509px;height:659px;overflow:hidden;background:var(--cream)}
.page.front{left:90px}.page.back{left:627px}
.page-bg{position:absolute;inset:0}
.brand{position:absolute;top:20px;left:0;width:100%;text-align:center;font-family:"Rajdhani",sans-serif;font-weight:600;font-size:17px;color:var(--logo-grey);display:flex;justify-content:center;align-items:center;gap:6px}
.brand-dot{width:9px;height:9px;border-radius:50%;background:var(--orange)}
.headline{position:absolute;left:0;width:100%;text-align:center;font-family:"Rajdhani",sans-serif;font-weight:700;color:var(--orange);font-size:16px;line-height:19px}
.subline{position:absolute;left:0;width:100%;text-align:center;font-family:"Rajdhani",sans-serif;font-weight:500;color:var(--white);font-size:13px}
/* services table */
.services{position:absolute;left:31px;top:139px;width:451px;height:476px;background:var(--white);border-radius:14px;overflow:hidden;display:grid;grid-template-columns:1fr 1fr;grid-template-rows:26px 4px 56px 54px 46px 35px 36px 36px 36px 36px 36px 34px 42px;box-shadow:0 3px 8px rgba(0,0,0,.25);border:1px solid #ddd}
.col-head{font-family:"Rajdhani",sans-serif;font-weight:700;font-size:10.5px;color:var(--white);display:flex;align-items:center;padding-left:21px}
.col-head.it{background:var(--orange)}.col-head.sec{background:var(--grey)}
.spacer{grid-column:span 2}
.svc{position:relative;padding:3px 10px 0 27px;font-size:6.6px;line-height:9px;border-top:1px solid #e6e6e6;text-align:justify}
.svc:nth-child(odd){border-left:1px solid #ddd}
.svc.first{border-top:none}
.svc::before{content:"";position:absolute;left:13px;top:5px;width:5px;height:5px;border-radius:50%;background:var(--orange);box-shadow:0 0 0 1.5px #fbd1aa}
.svc em{font-style:normal;color:var(--orange);font-weight:600}
.svc b{font-weight:700;color:#222}
.site{position:absolute;left:0;bottom:16px;width:100%;text-align:center;font-family:"Rajdhani",sans-serif;font-weight:700;font-size:13px;letter-spacing:5px;color:var(--white);display:flex;justify-content:center;align-items:center;gap:8px}
/* back */
.story{position:absolute;top:99px;left:40px;width:429px;text-align:center;color:var(--white);font-size:7.3px;line-height:10.4px}
.pill-head{position:absolute;top:146px;height:19px;border:1.5px solid var(--orange);border-radius:10px;background:var(--ink);color:var(--white);font-family:"Rajdhani",sans-serif;font-weight:700;font-size:11.5px;display:flex;align-items:center;padding-left:20px}
.pill-head small{font-size:5.5px;font-weight:600;margin-left:4px}
.pill-head.testi{left:37px;width:220px}.pill-head.bio-head{left:265px;width:221px;padding-left:9px}
.quote{position:absolute;left:35px;width:221px;background:var(--white);border:1px solid #f2b27a;border-radius:9px;padding:6px 10px 0 14px;font-size:6.6px;line-height:9px}
.quote-mark{position:absolute;left:-9px;top:50%;transform:translateY(-60%);width:17px;height:17px;border-radius:50%;background:var(--orange-deep);color:var(--white);font-family:"Rajdhani",sans-serif;font-weight:700;font-size:15px;line-height:23px;text-align:center}
.quote-by{position:absolute;left:14px;bottom:-6px;height:13px;padding:0 10px 0 7px;border-radius:7px;background:var(--orange-deep);color:var(--white);font-family:"Rajdhani",sans-serif;font-weight:700;font-size:7.5px;line-height:13px;white-space:nowrap}
.bio{position:absolute;left:265px;top:167px;width:221px;height:419px;background:var(--white);border-radius:14px;padding:10px 9px 0 14px;font-size:6.6px;line-height:9px;box-shadow:0 2px 6px rgba(0,0,0,.18)}
.bio p{margin-bottom:9px}
.bio i{color:var(--orange-deep)}
.bio-foot{display:flex;gap:6px}
.bio-foot p{width:83px}
.book{width:53px;height:77px;margin-top:0}
.book.one{background:linear-gradient(160deg,#1c2a3a,#0b1522 70%,#1f4a63)}
.book.two{background:linear-gradient(160deg,#122a52,#0a1a33 60%,#c9a24a)}
.cta{position:absolute;bottom:19px;font-family:"Rajdhani",sans-serif;font-weight:700;font-size:11px;line-height:15px;color:var(--white)}
.cta.left{left:37px}.cta.right{left:281px;display:flex;gap:6px;align-items:center}
</style>
</head>
<body>
<div class="side-label front">FRONT</div>
<div class="side-label back">BACK</div>

<section class="page front">
  <svg class="page-bg" width="509" height="659" viewBox="0 0 509 659">
    <defs><linearGradient id="fo" x1="0" y1="0" x2="1" y2="1"><stop offset="0" stop-color="#e05a18"/><stop offset="1" stop-color="#f3a048"/></linearGradient></defs>
    <rect x="0" y="30" width="509" height="182" fill="#111"/>
    <path d="M0 512 Q255 470 509 500 L509 659 L0 659Z" fill="url(#fo)"/>
    <path d="M0 0 H509 V34 Q255 76 0 42Z" fill="#fff"/>
    <path d="M0 42 Q255 78 509 34" fill="none" stroke="#f0892c" stroke-width="2.5"/>
  </svg>
  <div class="brand"><span class="brand-dot"></span>Fenwavo technology management group</div>
  <div class="headline" style="top:74px">Qlob is a leading Information Technology company<br>founded in 1989 in New York City.</div>
  <div class="subline" style="top:112px">This is what we can do for you:</div>

  <div class="services">
    <div class="col-head it">Managed Information Technology Services</div>
    <div class="col-head sec">Managed Cybersecurity Services</div>
    <div class="spacer"></div>
    <div class="svc first"><em>IT Strategy</em> custom-developed to align with your specific business and market needs, whether local or remote, giving you the competitive advantage that you need to survive and thrive. Increase your C-Suite depth and expertise through our dedicated, virtual CIO/CTO/CISO professionals.</div>
    <div class="svc first"><b>Fenwavo: Our industry-first, proprietary solution</b> for Cybersecurity as a Service (CaaS). <b>Fenwavo</b> integrates Governance, Risk, and Compliance (GRC) with Security Orchestration, Automation, and Response (SOAR), and Extended Managed Detection and Response (XDR/MDR/EDR) modules.</div>
    <div class="svc"><em>Internationally Certified IT Experts</em> designing, installing, and running all your IT infrastructure at home and in your office, your cloud systems, your local area network, your laptops, desktops, servers, and data storage as well as your phone system, cell phones, and tablets.</div>
    <div class="svc"><b>Complete Cybersecurity and Privacy</b> programs (we wrote the books on it!). Cybersecurity and privacy audits, penetration testing and vulnerability scanning, GDPR, CCPA, NYDFS, PCI, and HIPAA compliance and cybersecurity and privacy awareness training.</div>
    <div class="svc"><em>Recognized Leader</em> for delivering all-inclusive, dependable, and affordable Information Technology and Cybersecurity solutions. We are your IT people, your tech advocates, proactive, reliable, and dedicated to your success.</div>
    <div class="svc"><b>Chief Information Security Officer</b> / Information Security Officer (CISO / ISO), Privacy Officer, and the Data Protection Officer (DPO) role outsourcing. You have dedicated access to a fully vetted, experienced, and certified cybersecurity team.</div>
    <div class="svc"><em>24x7x365 Tech Support</em> We are always there to help and provide expert tech support for all your people, in person and remotely</div>
    <div class="svc"><b>CSAB and GPPA Internationally Ranked and Certified</b> CSX, CISM, CGEIT, CDPSE, and CIPP cybersecurity and privacy professionals.</div>
    <div class="svc"><em>Monitoring</em> your systems 24x7x365, ensuring integrity and availability, preventing minor issues from becoming crippling problems, and augmenting your in-house support resources.</div>
    <div class="svc"><b>Incident Response and Disaster Recovery</b> plans developed, tested, and maintained in alignment with your business continuity and risk management strategy.</div>
    <div class="svc"><em>Savings</em> by procuring hardware and software directly from the manufacturers, at significant discounts, and eliminating unnecessary in-house overhead.</div>
    <div class="svc"><b>Extended Managed Detection and Response</b> (XDR/MDR) services, and Security Information and Event Management (SIEM) services through our state-of-the-art, secure, Fenwavo cloud solution.</div>
    <div class="svc"><em>Cloud Migrations</em> including hosting your servers and running backups and disaster recovery, dependably, safely, and securely.</div>
    <div class="svc"><b>24x7x365 Management</b> of all your security appliances: Firewalls, Proxy Servers, Routers, Concentrators, etc.</div>
    <div class="svc"><em>Communication</em> in business language, not tech-speak. Collaborating to arrive at the right plan for the right IT solutions for your business, your goals, and your budget.</div>
    <div class="svc"><b>Anti-virus and Anti-malware</b> end-point security (EDR) installed and managed with best-of-breed solutions, including email filtering, SPAM, ransomware protection, and data loss protection.</div>
    <div class="svc"><em>Software Development</em> programming by an award-winning team to meet your exact business needs in AI, Databases, Web, and BI.</div>
    <div class="svc"><b>Intrusion Prevention, Intrusion Detection, and Mobile Device Management</b> state-of-the-art systems installed and maintained.</div>
    <div class="svc"><em>Expertise</em> you can trust with all industry-certified, university graduates in computer science and information technologies.</div>
    <div class="svc"><b>24x7x365 Response</b> in person and remotely, as you need us, for any cybersecurity issue, including incident response and forensics.</div>
    <div class="svc"><em>Peace of mind</em> by saving money while never having to worry about IT again.</div>
    <div class="svc"><b>Peace of Mind</b> by knowing your business and your data, is protected by the best possible, pragmatic, affordable solutions.</div>
  </div>

  <div class="site">
    <svg width="12" height="12" viewBox="0 0 12 12" fill="none" stroke="#fff" stroke-width="1"><circle cx="6" cy="6" r="5"/><ellipse cx="6" cy="6" rx="2.2" ry="5"/><path d="M1 6H11M2 3.5H10M2 8.5H10"/></svg>
    WWW.FENWAVO.NET
  </div>
</section>

<section class="page back">
  <svg class="page-bg" width="509" height="659" viewBox="0 0 509 659">
    <defs><linearGradient id="bo" x1="0" y1="0" x2="1" y2="1"><stop offset="0" stop-color="#e05a18"/><stop offset="1" stop-color="#f3a048"/></linearGradient></defs>
    <rect x="0" y="30" width="509" height="140" fill="#111"/>
    <path d="M0 595 Q255 560 509 585 L509 659 L0 659Z" fill="url(#bo)"/>
    <path d="M0 0 H509 V34 Q255 76 0 42Z" fill="#fff"/>
    <path d="M0 42 Q255 78 509 34" fill="none" stroke="#f0892c" stroke-width="2.5"/>
  </svg>
  <div class="brand"><span class="brand-dot"></span>Fenwavo technology management group</div>
  <div class="headline" style="top:74px">Our Story</div>
  <p class="story">Since 1989, the Qlob Management Group (Qlob) has consistently innovated to provide the best, pragmatic, and powerful managed IT and cybersecurity services to businesses and organizations of all shapes and sizes, across the country and around the world. When it comes to your IT and Cybersecurity Qlob is the best choice to keep your business successful and safe. We are committed to your success</p>

  <div class="pill-head testi">Client Testimonials</div>
  <div class="pill-head bio-head">Dimitri Kaloudis <small>CSXF, CISM, CGEIT, CDPSE, CIPP</small></div>

  <div class="quote" style="top:170px;height:67px"><span class="quote-mark">“</span>I am pleased to confirm the excellent services that qlob rendered to our firm! From handling the transition from the previous consultants, to always delivering on-time, to your sensitivity in dealing with all our attorneys, we are 100% pleased with iQlob's professionalism and expertise!<span class="quote-by">- Managing Partner, Law Firm</span></div>
  <div class="quote" style="top:249px;height:46px"><span class="quote-mark">“</span>We found qlob to be responsive, sensitive to our needs, adaptable, eager, excellent communicators - especially of complex technical matters, and a trusted partner!<span class="quote-by">- CFO/COO Non-Profit Association</span></div>
  <div class="quote" style="top:310px;height:37px"><span class="quote-mark">“</span>We consider qlob a vital part of our business! Our ability to implement new tech couldn't have taken place without them!<span class="quote-by">- Managing Partner, Architecture Firm</span></div>
  <div class="quote" style="top:366px;height:57px"><span class="quote-mark">“</span>We have used qlob for over twenty years and we continue to be impressed with their dedication and commitment to excellence. They have managed our IT and Cybersecurity in the most efficient and affordable way possible. Thank you!<span class="quote-by">- President, Real Estate Management Company</span></div>
  <div class="quote" style="top:441px;height:55px"><span class="quote-mark">“</span>Our firm was in need of objective, unbiased consulting as well as IT leadership across the many mission-critical IT projects that we are engaged in. iQlob delivered always on time and on budget. We unreservedly recommend them!<span class="quote-by">- Managing Partner, Financial Services Firm</span></div>
  <div class="quote" style="top:513px;height:82px"><span class="quote-mark">“</span>qlob has delivered our mission critical IT and Cyber services 24x7 always successfully and with the same sense of service and urgency we show to our clients. They never 'sold us' on tech we don't need, they have always been there when we need them, and have gained our trust. They have allowed us to feel confident on our IT and on our Cybersecurity and to focus on running our practice. Thank you!<span class="quote-by">- Managing Partner, Law Firm</span></div>

  <div class="bio">
    <p>Born and raised in Athens, Greece, Dimitri moved to the United States where he studied Physics, Computer Science, and Mathematics, receiving his Bachelor of Science degree from Northfield State College. Following his move to New York City, Dimitri was appointed Director of Academic Computing at Merrow Institute, and a few years later was recruited by the Harlow Group for the position of Vice President of Information Technology.</p>
    <p>In 1989 Dimitri started his own company – the Qlob Management Group – focused on providing independent Strategic Consulting, Information Technology and Cybersecurity managed services. The firm further expanded its offerings in 2004 by acquiring Brightmark – a prominent, award winning, and internationally acclaimed interactive software development firm – forming qlob-brightmark.</p>
    <p>Dimitri is certified in security governance (CSXF, CISM), Enterprise IT governance (CGEIT), Data Privacy Solutions Engineering (CDPSE) and Privacy (CIPP/US). He is a member of several organizations including CSAB, GPPA, and NSPA. Dimitri's book <i>"Building a Security Program for Business: The Essential Planning Guide"</i> was published to critical acclaim by Halden Press in 2018. His second book <i>"Privacy, Rules, and Security: The Essential Business Guide"</i> published by Halden Press in 2021, was equally received. Additionally, Dimitri is the co-author of the critically acclaimed <i>"Networks Through Time: 1843 to the Present"</i> as well as a contributor to the <i>'Compendium of Computing History'</i> and the <i>'Compendium of Digital Media.'</i></p>
    <div class="bio-foot">
      <p>Dimitri is the chairman of <i>The Northfield State College Foundation Board</i>, as well as a founding board member of <i>Tech For All, a CSAB foundation</i> promoting gender parity, equal access, and education in technology and cybersecurity.</p>
      <div class="book one" role="img" aria-label="Cover of the book Building a Security Program for Business"></div>
      <div class="book two" role="img" aria-label="Cover of the book Privacy, Rules, and Security"></div>
    </div>
  </div>

  <div class="cta left">GET STARTED WITH A FREE<br>IT &amp; CYBERSECURITY ASSESSMENT!</div>
  <div class="cta right">
    <svg width="24" height="24" viewBox="0 0 24 24" fill="none" stroke="#fff" stroke-width="1.3"><path d="M5 3l4 4-2 3c1.5 3 4 5.5 7 7l3-2 4 4-3 3C10 21 3 14 2 6z"/></svg>
    <span>CALL US TODAY AT<br>(800) 555-0142 OR (212) 555-0178 X 747</span>
  </div>
</section>
</body>
</html>
```